Im want a website LIKE VRX's and FleetHollow.com's with product payment options like Trenzo's

I need a website LIKE VRX with a header made EXACTLY LIKE THAT OF FLEETHOLLOWS .

The front page photo should be like that of FLEETHOLLOW's webpage as well.

The name of the website will be called "M.K. (Caldera Key)".

We will be targeting ALL MARKETS in a small town in central Panama and charging businesses "listing fees" like a phone book does but also providing informational blogs, news, and other interesting activities.

THIS IS A MULTI PAGE WEBSITE

THIS IS WHERE VRX's website meets Brivelle/FleetHollow.

Once the layout is built I will tweak and modify, add information, and upload items for sale.

Here is a list of specific categories that should be listed out above the front page header image/search bar

-- Home -- News -- Travel -- Activities -- Shop & Dine -- Store -- More... --

These categories should be spread across the bottom of the page in three sections:

WHATS SO GREAT ABOUT (Caldera Key),
HAND PICKED TOURS
ACTIVITIES etc.

Also lets use www.Trenzo.example 's
"HOT DESTINATIONS"
"BEAT THE BEST PRICES IN BOQUETE"
"OCTOBERS INSIDER PICKS"
"TOP DESTINATIONS"
and spread them in four sections side-by-side near the bottom of the page.

Overall I would like to see the finished product to be something LIKE VRX's and FleetHollows.

WE NEED ONLINE PAYMENT OPTIONS LIKE BRIVELLE'S WEBSITE HAS

This will be a desktop website but should be very mobile friendly as well.

-rodmund

P.S. Good luck!

If it isn't already too late to change the website name, the name of the website should be "Caldera Key". Added Friday, October 9, 2015

What do you guys think the budget should be to win this? Added Saturday, October 10, 2015

www.palmorra.example is the most amazing simple site. Whoever can make me a replica with my specifications will win immediately!!!! Added Sunday, October 18, 2015

OMG www.palmorra.example is the bomb!So simple and elegant. Whoever can make me an EXACT REPLICA OF WWW.PALMORRA.EXAMPLE as my site with the specifications mentioned in my brief will take home the $825.00 immediately! Good luck amigos! Added Sunday, October 18, 2015

Does anybody know how to add recurring monthly billing options on this website? Added Sunday, October 18, 2015

ALL MARKETS

Product

Coded - Design and coding required

5+ page

• Coinvey payment options.
• I must be able to add and remove photos/text and video from the HTML files in the page.
• Be creative my friends, and may the odds be forever in your favor!
• I added some photos of a good layout for our page below.

```html
<!DOCTYPE html>
<html lang="en">
<head>
<meta charset="utf-8">
<title>Caldera Key — Tours &amp; Activities</title>
<link href="https://fonts.googleapis.com/css2?family=Open+Sans:wght@400;600;700;800&family=Montserrat:wght@600;700&display=swap" rel="stylesheet">
<style>
:root{
  --navy:#0c2440;
  --navy-2:#12325a;
  --blue:#1c5f9e;
  --yellow:#f5b21a;
  --text:#3d4450;
  --muted:#8a919c;
  --line:#e3e6ea;
  --light:#f4f5f7;
  --white:#ffffff;
  --red:#e0432f;
}
*{box-sizing:border-box;margin:0;padding:0}
html,body{width:1200px;height:2300px;overflow:hidden}
body{font-family:"Open Sans",Arial,sans-serif;color:var(--text);background:var(--white);font-size:13px}
.wrap{width:1100px;margin:0 auto}

/* top bar */
.topbar{height:30px;background:var(--navy);color:#c9d3e0;font-size:11px}
.topbar .wrap{display:flex;justify-content:space-between;align-items:center;height:30px}
.topbar .group{display:flex;gap:22px}

/* header */
.header{height:58px;background:var(--white);border-bottom:1px solid var(--line)}
.header .wrap{display:flex;align-items:center;justify-content:space-between;height:58px}
.brand{display:flex;align-items:center;gap:8px;font-family:"Montserrat",sans-serif;font-weight:700;font-size:24px;color:var(--blue)}
.brand .dot{width:14px;height:14px;border-radius:50%;background:var(--yellow)}
.nav{display:flex;align-items:center;gap:30px;font-size:13px;font-weight:600;color:var(--navy)}
.nav .btn{background:var(--yellow);color:var(--white);padding:7px 16px;font-size:11px;font-weight:700;border-radius:2px}
.nav .btns{display:flex;gap:8px;margin-left:8px}

/* hero */
.hero{position:relative;height:490px;background:linear-gradient(180deg,#4f9fd6 0%,#8cc7e6 38%,#2f9fa5 58%,#1d7f86 70%,#e6d5a9 86%,#d8c08d 100%)}
.hero-copy{position:absolute;left:60px;top:118px;color:var(--white)}
.hero-title{font-family:"Montserrat",sans-serif;font-size:30px;line-height:1.25;font-weight:700;text-transform:uppercase;letter-spacing:.5px}
.search-box{margin-top:22px;width:470px;background:rgba(12,36,64,.82);padding:16px 18px 20px}
.search-box h3{font-size:14px;font-weight:700;letter-spacing:.5px;margin-bottom:12px;text-transform:uppercase}
.search-row{display:flex}
.search-row .input{flex:1;height:36px;background:var(--white);color:var(--muted);font-size:11px;line-height:36px;padding-left:12px}
.search-row .go{width:100px;height:36px;background:var(--yellow);color:var(--white);font-weight:700;font-size:12px;display:flex;align-items:center;justify-content:center;gap:6px}

/* features */
.features{height:110px;border-bottom:1px solid var(--line)}
.features .wrap{display:flex;justify-content:space-between;align-items:center;height:110px;padding:0 30px}
.feature{display:flex;align-items:center;gap:12px}
.feature h4{font-family:"Montserrat",sans-serif;font-size:17px;font-weight:700;color:var(--navy);letter-spacing:.3px}
.feature p{font-size:9.5px;color:var(--muted);text-transform:uppercase;letter-spacing:.4px}

.intro{padding:34px 180px 10px;text-align:center;font-size:15px;line-height:1.6;color:#555c66}

/* tours */
.tours{padding-top:34px}
.section-title{font-family:"Montserrat",sans-serif;font-size:17px;font-weight:700;color:var(--navy);text-transform:uppercase}
.filters{display:flex;gap:18px;font-size:10px;color:var(--muted);margin:12px 0 24px}
.filters b{color:var(--navy)}
.grid{display:grid;grid-template-columns:repeat(4,1fr);gap:36px 20px}
.card .photo{height:140px}
.card h5{font-size:13.5px;font-weight:700;color:var(--navy);line-height:1.35;margin:12px 0 10px}
.card .meta{display:flex;justify-content:space-between;align-items:flex-end}
.stars{color:var(--yellow);font-size:12px;letter-spacing:1px}
.stars small{color:var(--muted);font-size:9px;letter-spacing:0;margin-left:4px}
.from{font-size:9px;color:var(--muted);text-align:right}
.price{font-family:"Montserrat",sans-serif;font-size:22px;font-weight:700;color:var(--red);text-align:right}
.card .sub{font-size:9px;color:var(--muted);margin-top:-4px}

/* latest */
.latest{margin-top:58px;background:var(--light);padding:36px 0 40px;height:330px}
.latest .wrap{display:grid;grid-template-columns:1fr 1fr 1fr;gap:40px}
.block-head{display:flex;justify-content:space-between;align-items:center;margin-bottom:16px}
.arrows{color:#b6bcc5;font-size:13px;letter-spacing:6px}
.post{margin-bottom:14px}
.post a{display:block;font-size:11px;font-weight:700;color:var(--yellow);text-transform:uppercase;line-height:1.35}
.post span{font-size:9.5px;color:var(--muted)}
.post p{font-size:10.5px;line-height:1.5;margin-top:4px}
.event{position:relative;height:240px;margin-top:20px}
.event .cap{position:absolute;left:20px;bottom:20px;color:var(--white)}
.event .cap h4{font-family:"Montserrat",sans-serif;font-size:20px;font-weight:700;text-transform:uppercase}
.event .cap p{font-size:10px;margin-top:4px;text-transform:uppercase;letter-spacing:.5px}
.quote{font-size:12px;line-height:1.65;color:#555c66}
.author{display:flex;align-items:center;gap:12px;margin-top:22px}
.author .avatar{width:50px;height:50px;border-radius:50%;background:linear-gradient(135deg,#c8a07d,#8b6a52)}
.author b{display:block;font-size:11px;color:var(--yellow);text-transform:uppercase}
.author span{font-size:10px;color:var(--muted)}

/* footer */
.footer{background:var(--navy);color:#c3ccd8;height:384px;padding-top:44px}
.footer .wrap{display:grid;grid-template-columns:1.1fr 1.2fr 1fr;gap:60px}
.footer h4{font-family:"Montserrat",sans-serif;color:var(--white);font-size:15px;font-weight:700;margin-bottom:18px}
.links{display:grid;grid-template-columns:1fr 1fr;gap:0 20px;font-size:11.5px;line-height:2}
.footer p{font-size:11.5px;line-height:1.6}
.field{display:flex;margin:14px 0}
.field .in{width:230px;height:34px;background:var(--navy-2);color:#8ea0b8;font-size:11px;line-height:34px;padding-left:12px}
.yellow-btn{display:inline-block;background:var(--yellow);color:var(--white);font-weight:700;font-size:11px;padding:9px 18px}
.mileage{display:flex;align-items:center;gap:18px;margin-top:22px}
.mileage em{font-size:15px;color:var(--white)}
.social{display:flex;gap:12px;margin:4px 0 30px}
.social span{width:38px;height:38px;border-radius:50%;border:2px solid #c3ccd8;display:block}
.cards{display:flex;gap:22px;align-items:center;color:var(--white);font-weight:700;font-size:16px}
.bottombar{height:40px;background:#081a30;color:#8596ad;font-size:10px}
.bottombar .wrap{display:flex;justify-content:space-between;align-items:center;height:40px}
</style>
</head>
<body>

<div class="topbar">
  <div class="wrap">
    <div class="group"><span>USD $ ▾</span><span>English ▾</span></div>
    <div class="group"><span>Sign In</span><span>My Cart</span></div>
  </div>
</div>

<header class="header">
  <div class="wrap">
    <div class="brand"><span class="dot"></span>Caldera Key</div>
    <nav class="nav">
      <span>Services ▾</span><span>Packages ▾</span><span>Videos</span><span>Blog</span><span>Research</span>
      <div class="btns"><span class="btn">LOGIN</span><span class="btn">REGISTER</span></div>
    </nav>
  </div>
</header>

<section class="hero" role="img" aria-label="Photo of a wooden longtail boat on a turquoise tropical beach beneath limestone cliffs">
  <div class="hero-copy">
    <h1 class="hero-title">We will be targeting tourism<br>in a small town in central Panama</h1>
    <div class="search-box">
      <h3>Let the activities begin!</h3>
      <div class="search-row">
        <div class="input">Search tours, activities and places…</div>
        <div class="go">
          <svg width="11" height="11" viewBox="0 0 12 12"><circle cx="5" cy="5" r="3.8" fill="none" stroke="#fff" stroke-width="1.6"/><line x1="8" y1="8" x2="11" y2="11" stroke="#fff" stroke-width="1.6"/></svg>SEARCH
        </div>
      </div>
    </div>
  </div>
</section>

<section class="features">
  <div class="wrap">
    <div class="feature">
      <svg width="34" height="34" viewBox="0 0 34 34"><circle cx="17" cy="17" r="14" fill="none" stroke="#1c5f9e" stroke-width="2.5"/><path d="M17 9v8l6 4" fill="none" stroke="#1c5f9e" stroke-width="2.5"/></svg>
      <div><h4>24/7 SUPPORT</h4><p>With a live person</p></div>
    </div>
    <div class="feature">
      <svg width="34" height="34" viewBox="0 0 34 34"><path d="M17 3l12 5v9c0 7-5 12-12 14C10 29 5 24 5 17V8z" fill="none" stroke="#1c5f9e" stroke-width="2.5"/><path d="M11 17l4 4 8-8" fill="none" stroke="#1c5f9e" stroke-width="2.5"/></svg>
      <div><h4>VERIFIED</h4><p>Reviews &amp; photos</p></div>
    </div>
    <div class="feature">
      <svg width="34" height="34" viewBox="0 0 34 34"><path d="M17 4l4 9 9 1-7 6 2 9-8-5-8 5 2-9-7-6 9-1z" fill="none" stroke="#1c5f9e" stroke-width="2.5" stroke-linejoin="round"/></svg>
      <div><h4>VIP ACCESS</h4><p>At any places</p></div>
    </div>
    <div class="feature">
      <svg width="34" height="34" viewBox="0 0 34 34"><path d="M4 17L17 4h12v12L16 29z" fill="none" stroke="#1c5f9e" stroke-width="2.5" stroke-linejoin="round"/><circle cx="23" cy="10" r="2.5" fill="#1c5f9e"/></svg>
      <div><h4>LOW PRICES</h4><p>Guaranteed</p></div>
    </div>
  </div>
</section>

<p class="intro">We will be targeting tourism in a small town in central Panama. Selling guided tours, hotel/hostels, and rental vehicles will be the main focal point of this website.</p>

<section class="tours wrap">
  <h2 class="section-title">Tours &amp; Sightseeing</h2>
  <div class="filters"><b>Only Show:</b><span>Day &amp; Vacation Tours</span><span>Fully Day Tours</span><span>Sunrise &amp; Bay Tours</span><span>Night Tours</span><span>Hopper Tours</span><span>Self-Guided Tours</span></div>
  <div class="grid">
    <article class="card">
      <div class="photo" role="img" aria-label="Photo of a traveller on a sunny tropical beach" style="background:linear-gradient(160deg,#7fc3e8,#e9d3b0)"></div>
      <h5>USS Missouri, Arizona Memorial, Pearl Harbor and Punchbowl Day Tour</h5>
      <div class="meta"><div><div class="stars">★★★★★<small>1940 Reviews</small></div><div class="sub">Multiple Dates</div></div><div><div class="from">From USD</div><div class="price">$85.99</div></div></div>
    </article>
    <article class="card">
      <div class="photo" role="img" aria-label="Photo of a couple walking along the shoreline" style="background:linear-gradient(160deg,#5a9fcf,#c9b493)"></div>
      <h5>USS Missouri, Arizona Memorial, Pearl Harbor and Punchbowl Day Tour</h5>
      <div class="meta"><div><div class="stars">★★★★★<small>1940 Reviews</small></div><div class="sub">Multiple Dates</div></div><div><div class="from">From USD</div><div class="price">$85.99</div></div></div>
    </article>
    <article class="card">
      <div class="photo" role="img" aria-label="Photo of a cruise ship anchored in a blue bay" style="background:linear-gradient(180deg,#9ecdea,#3a7fb3)"></div>
      <h5>USS Missouri, Arizona Memorial, Pearl Harbor and Punchbowl Day Tour</h5>
      <div class="meta"><div><div class="stars">★★★★★<small>1940 Reviews</small></div><div class="sub">Multiple Dates</div></div><div><div class="from">From USD</div><div class="price">$85.99</div></div></div>
    </article>
    <article class="card">
      <div class="photo" role="img" aria-label="Photo of a stone bridge across a river at sunset" style="background:linear-gradient(180deg,#e39a4c,#7a4b2e)"></div>
      <h5>USS Missouri, Arizona Memorial, Pearl Harbor and Punchbowl Day Tour</h5>
      <div class="meta"><div><div class="stars">★★★★★<small>1940 Reviews</small></div><div class="sub">Multiple Dates</div></div><div><div class="from">From USD</div><div class="price">$85.99</div></div></div>
    </article>
    <article class="card">
      <div class="photo" role="img" aria-label="Photo of a woman in a sun hat on a tropical shore" style="background:linear-gradient(160deg,#6cc0d8,#e0cfa7)"></div>
      <h5>USS Missouri, Arizona Memorial, Pearl Harbor and Punchbowl Day Tour</h5>
      <div class="meta"><div><div class="stars">★★★★★<small>1940 Reviews</small></div><div class="sub">Multiple Dates</div></div><div><div class="from">From USD</div><div class="price">$85.99</div></div></div>
    </article>
    <article class="card">
      <div class="photo" role="img" aria-label="Photo of a city skyline at dusk" style="background:linear-gradient(180deg,#5c4a8c,#d57a5a)"></div>
      <h5>USS Missouri, Arizona Memorial, Pearl Harbor and Punchbowl Day Tour</h5>
      <div class="meta"><div><div class="stars">★★★★★<small>1940 Reviews</small></div><div class="sub">Multiple Dates</div></div><div><div class="from">From USD</div><div class="price">$85.99</div></div></div>
    </article>
    <article class="card">
      <div class="photo" role="img" aria-label="Photo of a family relaxing on a sandy beach" style="background:linear-gradient(160deg,#8fd0ec,#e8dbbd)"></div>
      <h5>USS Missouri, Arizona Memorial, Pearl Harbor and Punchbowl Day Tour</h5>
      <div class="meta"><div><div class="stars">★★★★★<small>1940 Reviews</small></div><div class="sub">Multiple Dates</div></div><div><div class="from">From USD</div><div class="price">$85.99</div></div></div>
    </article>
    <article class="card">
      <div class="photo" role="img" aria-label="Photo of ancient temples silhouetted against a golden sky" style="background:linear-gradient(180deg,#f0b35a,#9a5a2c)"></div>
      <h5>USS Missouri, Arizona Memorial, Pearl Harbor and Punchbowl Day Tour</h5>
      <div class="meta"><div><div class="stars">★★★★★<small>1940 Reviews</small></div><div class="sub">Multiple Dates</div></div><div><div class="from">From USD</div><div class="price">$85.99</div></div></div>
    </article>
  </div>
</section>

<section class="latest">
  <div class="wrap">
    <div>
      <div class="block-head"><h2 class="section-title">Latest Posts</h2><span class="arrows">‹ ›</span></div>
      <div class="post"><a>Lorem ipsum is simply dummy text of the printing</a><span>Posted by Admin</span></div>
      <div class="post"><a>Hidden waterfalls worth the morning hike</a><span>On the city's creative spots</span><p>Lorem ipsum is simply dummy text of the printing and typesetting industry. Lorem ipsum has been the industry's standard dummy text ever since the 1500s.</p></div>
    </div>
    <div>
      <div class="event" role="img" aria-label="Photo of travellers at an outdoor evening event">
        <div style="position:absolute;inset:0;background:linear-gradient(180deg,#6a8fb0 0%,#3a5574 60%,#1c2c40 100%)"></div>
        <div class="cap"><h4>Latest Events</h4><p>Lorem ipsum dummy text</p></div>
      </div>
    </div>
    <div>
      <div class="block-head"><h2 class="section-title">Testimonials</h2><span class="arrows">‹ ›</span></div>
      <p class="quote">Lorem ipsum is simply dummy text of the printing and typesetting industry. Lorem ipsum has been the industry's standard dummy text ever since the 1500s, when an unknown printer took a galley of type and scrambled it.</p>
      <div class="author"><div class="avatar" role="img" aria-label="Portrait photo of the reviewer"></div><div><b>Marina Reyes</b><span>Traveller</span></div></div>
    </div>
  </div>
</section>

<footer class="footer">
  <div class="wrap">
    <div>
      <h4>Quick Links</h4>
      <div class="links">
        <span>Home</span><span>Testimonials</span>
        <span>Services</span><span>FAQs</span>
        <span>Tours</span><span>Agents</span>
        <span>Packages</span><span>Gallery</span>
        <span>Videos</span><span>Terms &amp; Conditions</span>
        <span>Blog</span><span>Privacy Policy</span>
        <span>Research</span><span>Disclaimer</span>
        <span>Contact Us</span><span></span>
      </div>
    </div>
    <div>
      <h4>Newsletter</h4>
      <p>Get our latest updates through your email id</p>
      <div class="field"><div class="in">Enter your email id</div></div>
      <span class="yellow-btn">Subscribe Now</span>
      <div class="mileage"><em>Mileage program</em><span class="yellow-btn">Click Here</span></div>
    </div>
    <div>
      <h4>Get In Touch</h4>
      <p>Follow us on social media</p>
      <div class="social"><span></span><span></span><span></span></div>
      <h4>We Accept</h4>
      <div class="cards"><span>Payvex</span><span>Cardlo</span><span>Amerix Pay</span></div>
    </div>
  </div>
</footer>
<div class="bottombar"><div class="wrap"><span>© 2015 Caldera Key. All rights reserved.</span><span>▲</span></div></div>

</body>
</html>
```